Hollow Thicket, a 3d voxel survival video game needs a card for gaming conventions

I am the lead developer for Hollow Thicket http://www.HollowThicket.example and need a business card to hand out at an indie gaming convention
The card would need to include the game name, website url, my name, position (Lead Developer), e-mail and phone number
The game is a 3d, voxel (with smooth terrain) based survival game with guns and wildlife. The main icon of the game would likely be a grizzly bear but I am willing to accept other designs too.
Attached is a media kit for the game with some images you can use but don't have to its just what little art I can provide. Anything on the website or from the video game can also be used. unrelated art can also be used.
Target Market(s)
Indie Developers/publishers at conferences
Industry/Entity Type
Games
Contact Information for Business Card
Name: Corin Waldrick
Position: Lead Developer
E-mail: Pale_Kettle@mailbox.example
Phone number: 555-372-1186

```html
<!DOCTYPE html>
<html lang="en">
<head>
<meta charset="utf-8">
<title>Hollow Thicket – Business Card</title>
<link rel="stylesheet" href="https://fonts.googleapis.com/css2?family=Ubuntu:wght@500;700&family=Open+Sans:wght@400;600&display=swap">
<style>
  :root {
    --backdrop: #e9e5de;
    --card: #ffffff;
    --card-edge: #f1f1f1;
    --brand-green: #3f6b34;
    --name-red: #d8322b;
    --title-tan: #c9aa62;
    --ink: #1a1a1a;
    --photo-light: #e4dfd2;
    --photo-mid: #b9b298;
    --photo-dark: #8d876c;
    --wave: #121212;
  }
  * { box-sizing: border-box; margin: 0; padding: 0; }
  html, body { width: 1200px; height: 858px; overflow: hidden; }
  body {
    background: var(--backdrop);
    position: relative;
    font-family: "Open Sans", sans-serif;
  }
  .card {
    position: absolute;
    left: 270px;
    width: 660px;
    height: 378px;
    background: radial-gradient(ellipse at 55% 45%, var(--card) 55%, var(--card-edge) 100%);
    box-shadow: 0 6px 18px rgba(0,0,0,0.18);
    overflow: hidden;
  }
  .card--front { top: 32px; }
  .card--back { top: 446px; }

  .front-art { position: absolute; inset: 0; }

  .front-content {
    position: absolute;
    left: 300px;
    top: 0;
    right: 0;
    bottom: 0;
  }
  .brand-name {
    position: absolute;
    left: 6px;
    top: 34px;
    font-family: "Ubuntu", sans-serif;
    font-weight: 700;
    font-size: 44px;
    line-height: 1.0;
    letter-spacing: 2px;
    text-transform: uppercase;
    color: var(--brand-green);
  }
  .person {
    position: absolute;
    left: 96px;
    top: 150px;
  }
  .person-name {
    font-family: "Ubuntu", sans-serif;
    font-weight: 500;
    font-size: 19px;
    letter-spacing: 1px;
    color: var(--name-red);
  }
  .person-title {
    font-family: "Ubuntu", sans-serif;
    font-weight: 500;
    font-size: 14px;
    letter-spacing: 1px;
    color: var(--title-tan);
    margin-top: 2px;
    margin-left: 22px;
  }
  .contact {
    position: absolute;
    right: 22px;
    bottom: 26px;
    list-style: none;
    text-align: right;
  }
  .contact li {
    display: flex;
    align-items: center;
    justify-content: flex-end;
    gap: 10px;
    font-size: 16px;
    color: var(--ink);
    line-height: 1.6;
    white-space: nowrap;
  }
  .contact-icon {
    width: 14px;
    height: 14px;
    flex: none;
    background: var(--title-tan);
    border-radius: 2px;
    display: inline-flex;
    align-items: center;
    justify-content: center;
  }

  .back-brand {
    position: absolute;
    left: 0; right: 0;
    top: 50%;
    transform: translateY(-50%);
    text-align: center;
    font-family: "Ubuntu", sans-serif;
    font-weight: 700;
    font-size: 82px;
    line-height: 1.0;
    letter-spacing: 4px;
    text-transform: uppercase;
    color: var(--brand-green);
  }
</style>
</head>
<body>

<section class="card card--front" aria-label="Card front">
  <svg class="front-art" width="660" height="378" viewBox="0 0 660 378">
    <defs>
      <radialGradient id="photoTone" cx="55%" cy="35%" r="80%">
        <stop offset="0" stop-color="var(--photo-light)"/>
        <stop offset="0.55" stop-color="var(--photo-mid)"/>
        <stop offset="1" stop-color="var(--photo-dark)"/>
      </radialGradient>
    </defs>
    <path class="photo-area" role="img" aria-label="Grizzly bear standing on a rock"
          d="M0 0 H250 C300 90 230 250 300 378 H0 Z" fill="url(#photoTone)"/>
    <path class="wave-divider" d="M250 0 C300 90 230 250 300 378"
          fill="none" stroke="var(--wave)" stroke-width="9"/>
    <path d="M262 0 C310 90 242 250 312 378"
          fill="none" stroke="var(--wave)" stroke-width="2" opacity="0.6"/>
  </svg>

  <div class="front-content">
    <h1 class="brand-name">Hollow<br>Thicket</h1>
    <div class="person">
      <p class="person-name">Corin Waldrick</p>
      <p class="person-title">Lead Developer</p>
    </div>
    <ul class="contact">
      <li>555-372-1186
        <span class="contact-icon">
          <svg width="9" height="9" viewBox="0 0 10 10"><path d="M2 1 L4 3 L3 4 Q4 6 6 7 L7 6 L9 8 L8 9 Q3 9 1 2 Z" fill="#fff"/></svg>
        </span>
      </li>
      <li>Pale_Kettle@mailbox.example
        <span class="contact-icon">
          <svg width="9" height="9" viewBox="0 0 10 10"><rect x="1" y="2.5" width="8" height="5.5" fill="none" stroke="#fff" stroke-width="1"/><path d="M1 2.5 L5 6 L9 2.5" fill="none" stroke="#fff" stroke-width="1"/></svg>
        </span>
      </li>
      <li>www.HollowThicket.example
        <span class="contact-icon">
          <svg width="9" height="9" viewBox="0 0 10 10"><circle cx="5" cy="5" r="4" fill="none" stroke="#fff" stroke-width="1"/><ellipse cx="5" cy="5" rx="1.8" ry="4" fill="none" stroke="#fff" stroke-width="0.8"/><path d="M1 5 H9" stroke="#fff" stroke-width="0.8"/></svg>
        </span>
      </li>
    </ul>
  </div>
</section>

<section class="card card--back" aria-label="Card back">
  <h2 class="back-brand">Hollow<br>Thicket</h2>
</section>

</body>
</html>
```